Business Cards for IT Consulting Company (Managed Service Provider)

I am looking to have some business cards printed and would like some designs. We are an IT Consulting company based in Vancouver BC. I would like a nice clean and modern look to the cards. I have uploaded all the versions of my logo so parts can be used as needed. Here is a snippit from our website homepage:

Quillbrook Networks Ltd. is an IT Solutions Partner located in Vancouver BC, Canada. We offer IT solutions and support to customers in the greater Vancouver Area. With expertise in Microsoft platforms, as well as Linux and Mac OSX and over 12 years experience in the IT industry, Quillbrook Networks is dedicated to offering our clients top quality service and products. We take pride in the solutions we offer our customers. The greatest compliment a client can give us is to recommend our services.

Quillbrook Networks Ltd. offers a wide range of IT services from onsite service to remote support and managed service solutions. This allows clients to choose the support path that best suits their company’s needs. Supporting many different sized companies from small to enterprise level over the past 12 years Quillbrook Networks has the experience and expertise needed to ensure things run smoothly. Allowing our clients to focus on doing business.

Revolutionizing the way IT services are delivered.

Quillbrook Networks is dedicated to providing our clients with IT solutions that work and grow with them for years to come. This philosophy helps save money in the long run instead of replacing equipment constantly. Far too often IT solutions are not well thought out and while possibly solving the problem at hand, require replacement due to growth or quality within a very short time frame. Quillbrook Networks takes pride in providing solutions that will last and be able to accommodate growth without the need for replacement.

Industry/Entity Type

Information Technology

Contact Information for Business Card

Quillbrook Networks Ltd.
(Employee Name)
Eml: (Employees Email Address)
Web: quillbrook.me
Ph: 604-555-0148

Font styles to use
Serif
Sans Serif

Requirements
Must have
• The Company logo and company colors.
Nice to have
• - Our tag line: "Revolutionizing IT Services" or "Revolutionizing the way IT services are delivered."
• - Also I really like the idea of nature and technology together blending which is sort of where my logo came from so integrating that somehow onto the business cards would be great.

```html
<!DOCTYPE html>
<html lang="en">
<head>
<meta charset="utf-8">
<title>Quillbrook Networks Ltd. – Business Cards</title>
<link rel="stylesheet" href="https://fonts.googleapis.com/css2?family=Montserrat:wght@500&family=Roboto:ital,wght@0,400;0,500;1,400&display=swap">
<style>
  :root {
    --backdrop: #aeacad;
    --card: #1d1d1e;
    --brand-blue: #1a8ad4;
    --band-blue: #1990d6;
    --swoosh-grey: #5b595a;
    --text-light: #e6e6e6;
    --text-muted: #c9c9c9;
  }
  * { margin: 0; padding: 0; box-sizing: border-box; }
  html, body { width: 1200px; height: 1200px; overflow: hidden; }
  body {
    position: relative;
    background: var(--backdrop);
    font-family: "Roboto", Arial, sans-serif;
  }
  .card {
    position: absolute;
    width: 712px;
    background: var(--card);
    overflow: hidden;
  }
  .card--front { left: 238px; top: 117px; height: 420px; }
  .card--back  { left: 231px; top: 644px; height: 416px; }

  .brand-name {
    font-family: "Montserrat", Arial, sans-serif;
    font-weight: 500;
    color: var(--brand-blue);
    white-space: nowrap;
  }
  .card--front .brand-name {
    position: absolute;
    left: 0; right: 0; top: 170px;
    text-align: center;
    font-size: 42px;
  }
  .front-tagline {
    position: absolute;
    left: 0; right: 0; top: 377px;
    display: flex;
    justify-content: center;
    align-items: center;
    gap: 16px;
    color: var(--text-light);
    font-size: 19px;
  }
  .front-tagline .rule {
    width: 110px; height: 3px;
    background: linear-gradient(90deg, transparent, var(--brand-blue) 40%);
    border-radius: 2px;
  }
  .front-tagline .rule--right {
    background: linear-gradient(270deg, transparent, var(--brand-blue) 40%);
  }

  .back-wave { position: absolute; left: 0; top: 0; }
  .back-tagline {
    position: absolute;
    right: 37px; top: 30px;
    text-align: right;
    color: #ffffff;
    font-size: 18px;
    line-height: 25px;
  }
  .card--back .brand-name {
    position: absolute;
    left: 32px; top: 150px;
    font-size: 34px;
  }
  .contact-list {
    position: absolute;
    left: 52px; top: 288px;
    list-style: none;
  }
  .contact-list li {
    display: flex;
    align-items: center;
    gap: 16px;
    height: 27px;
    color: var(--text-muted);
    font-size: 18px;
  }
  .contact-list svg { width: 17px; height: 17px; flex: none; }
  .holder {
    position: absolute;
    right: 37px; top: 303px;
    text-align: right;
  }
  .holder-name {
    color: var(--brand-blue);
    font-weight: 500;
    font-size: 25px;
  }
  .holder-role {
    margin-top: 4px;
    color: var(--text-muted);
    font-style: italic;
    font-size: 16px;
  }
</style>
</head>
<body>

<section class="card card--front">
  <div class="brand-name">Quillbrook Networks Ltd.</div>
  <div class="front-tagline">
    <span class="rule"></span>
    <span>Revolutionizing IT Services</span>
    <span class="rule rule--right"></span>
  </div>
</section>

<section class="card card--back">
  <svg class="back-wave" width="712" height="200" viewBox="0 0 712 200" aria-hidden="true">
    <path d="M0 0 H712 V150 C610 150 560 120 480 78 C380 25 200 8 0 45 Z" fill="var(--band-blue)"/>
    <path d="M0 82 C160 38 340 30 470 92 C570 142 630 170 712 172" fill="none" stroke="var(--swoosh-grey)" stroke-width="9"/>
  </svg>

  <p class="back-tagline">Revolutionizing the<br>way IT services<br>are delivered</p>

  <div class="brand-name">Quillbrook Networks Ltd.</div>

  <ul class="contact-list">
    <li>
      <svg viewBox="0 0 20 20"><path fill="var(--brand-blue)" d="M2 7c0-2 3-4 8-4s8 2 8 4v2h-4V7.5c-1-.6-2.5-.9-4-.9s-3 .3-4 .9V9H2zM5 10h10l2 6H3zm5 1.5a2 2 0 1 0 0 4 2 2 0 0 0 0-4z"/></svg>
      <span>604-555-0148</span>
    </li>
    <li>
      <svg viewBox="0 0 20 20"><g fill="none" stroke="var(--brand-blue)" stroke-width="1.6"><circle cx="10" cy="10" r="8"/><ellipse cx="10" cy="10" rx="3.5" ry="8"/><path d="M2 10h16M3.5 6h13M3.5 14h13"/></g></svg>
      <span>www.quillbrook.me</span>
    </li>
    <li>
      <svg viewBox="0 0 20 20"><rect x="1.5" y="4" width="17" height="12" fill="var(--brand-blue)"/><path d="M1.5 4l8.5 7 8.5-7" fill="none" stroke="var(--card)" stroke-width="1.5"/></svg>
      <span>support@quillbrook.me</span>
    </li>
  </ul>

  <div class="holder">
    <div class="holder-name">Daniel Hartley</div>
    <div class="holder-role">Managing Director</div>
  </div>
</section>

</body>
</html>
```